Website for my law practice

I am a solo practitioner, who specializes in family law and estate planning in Massachusetts. I need to re-do my website, as it is outdated. I like the idea of a nontraditional law firm website. My website address is: doloresquintanalaw.com. I would like to retain my logo in the green color, as part of the new website. I have uploaded my logo below.

My hourly rate has changed from what is listed on my current website. My new hourly rate is $385.00. Please use this hourly rate when creating the website.

Good morning,

I have reviewed the designs submitted so far. I am happy that the "dq" logo in the green color is part of each of the designs submitted. I am also happy that the standard items seen in law firm websites, such as the scales of justice, etc. were not incorporated. Although the green logo is great, I do not think rest of the website has to have the same green color throughout. Additionally, I was hoping for something more creative, to make the website standout and not the stock web designs you see everyday. Please incorporate more unique images if you can. For example of what I mean, please look at this website: https://www.rosalindfenwicklaw.com

```html
<!DOCTYPE html>
<html lang="en">
<head>
<meta charset="utf-8">
<title>Dolores Quintana – Attorney at Law</title>
<link href="https://fonts.googleapis.com/css2?family=Jost:wght@400;500;600&family=Roboto:wght@400;500;700&display=swap" rel="stylesheet">
<style>
:root{
  --green:#46872f;
  --green-soft:#e4ece0;
  --ink:#111111;
  --text:#333333;
  --grey-bg:#f4f4f4;
  --white:#ffffff;
}
*{box-sizing:border-box;margin:0;padding:0}
html,body{width:1200px;height:2855px;overflow:hidden;background:var(--white)}
body{font-family:"Roboto",sans-serif;color:var(--text)}
.page{position:relative;width:1200px;height:2855px;overflow:hidden}
.abs{position:absolute}
.topline{left:0;top:0;width:1200px;height:5px;background:var(--green)}
/* brand */
.brand{display:flex;align-items:center;gap:12px}
.brand-dot{width:52px;height:52px;border:5px solid var(--green);border-radius:50%;flex:none}
.brand-name{font-family:"Jost",sans-serif;font-weight:500;color:var(--green);line-height:1.2;white-space:nowrap}
.site-brand{left:111px;top:38px}
.site-brand .brand-name{font-size:15px}
/* nav */
.nav{top:50px;left:388px;display:flex;align-items:center;height:32px;font-size:13.5px;font-weight:500;color:var(--ink)}
.nav a{color:inherit;text-decoration:none;margin-right:34px}
.nav .active{background:var(--green);color:var(--white);padding:8px 18px;border-radius:20px;margin-right:18px}
.call-icon{left:903px;top:40px;width:50px;height:50px;border-radius:50%;background:var(--white);box-shadow:0 4px 14px rgba(0,0,0,.12);display:flex;align-items:center;justify-content:center}
.call{left:968px;top:47px}
.call small{display:block;font-size:11px;font-weight:700;color:var(--ink)}
.call strong{display:block;font-size:21px;font-weight:700;color:var(--green);margin-top:2px}
/* hero */
.hero-art{left:0;top:123px}
.hero-title{left:111px;top:240px;font-family:"Jost",sans-serif;font-size:42px;line-height:1.2;font-weight:600;color:var(--ink);white-space:nowrap}
.hero-title span{display:block;font-weight:400;color:var(--green)}
.rule{width:75px;height:4px;background:var(--green)}
.hero-rule{left:111px;top:346px}
.hero-text{left:111px;top:372px;width:555px;font-size:19px;line-height:1.5;color:var(--ink)}
.btn{display:flex;align-items:center;justify-content:center;background:var(--green);color:var(--white);font-weight:700;font-size:15px;border-radius:30px;text-transform:uppercase;white-space:nowrap}
.hero-btn{left:111px;top:452px;width:298px;height:50px}
.dots{left:53px;top:292px;display:flex;flex-direction:column;gap:14px}
.dots i{display:block;width:12px;height:12px;border-radius:50%;background:#bdbdbd}
.dots i.on{background:var(--green)}
.hero-badge{left:559px;top:649px;width:82px;height:82px;border-radius:50%;background:var(--white);box-shadow:0 6px 16px rgba(0,0,0,.15);display:flex;align-items:center;justify-content:center;font-family:"Jost",sans-serif;font-weight:500;font-size:15px;color:var(--green)}
/* about */
.portrait{left:111px;top:789px;width:446px;height:446px;border-radius:50%;border:7px solid var(--green);padding:10px;background:var(--white)}
.portrait div{width:100%;height:100%;border-radius:50%;background:radial-gradient(circle at 50% 45%,#c9c9c9,#7d7d7d 65%,#3f3f3f)}
.sec-title{font-family:"Jost",sans-serif;font-size:40px;font-weight:600;color:var(--ink);line-height:1.1;white-space:nowrap}
.sec-title span{font-weight:400;color:var(--green)}
.about-title{left:600px;top:818px}
.about-rule{left:600px;top:865px}
.body-text{font-size:15.3px;line-height:25px;text-align:justify;color:var(--text)}
.body-text p+p{margin-top:14px}
.about-text{left:600px;top:900px;width:489px}
.about-btn{left:600px;top:1149px;width:152px;height:48px}
/* tabs */
.tab{top:1333px;width:600px;height:85px;display:flex;align-items:center;justify-content:center;color:var(--white);font-weight:700;font-size:21px}
.tab-family{left:0;background:var(--ink)}
.tab-estate{left:600px;background:var(--green)}
.tab-pointer{left:890px;top:1417px;width:0;height:0;border-left:10px solid transparent;border-right:10px solid transparent;border-top:14px solid var(--green)}
/* estate */
.estate-title{left:111px;top:1516px}
.estate-rule{left:111px;top:1563px}
.estate-text{left:111px;top:1598px;width:489px}
.estate-btn{left:111px;top:1846px;width:153px;height:49px}
.estate-back{left:687px;top:1491px;width:419px;height:420px;border-radius:18px;background:var(--green-soft)}
.estate-img{left:668px;top:1508px;width:420px;height:420px;border-radius:18px;background:linear-gradient(135deg,#c8b98c 0%,#e2b73a 40%,#eef1f3 70%,#6fa9cc 100%)}
/* contact */
.contact{left:0;top:2027px;width:1200px;height:445px;background:var(--grey-bg)}
.contact-title{left:0;top:2090px;width:1200px;text-align:center}
.contact-rule{left:563px;top:2138px}
.field{height:49px;background:var(--white);box-shadow:0 4px 12px rgba(0,0,0,.06);border-radius:3px;padding:16px 17px;font-size:15px;color:var(--ink)}
.f-name{left:165px;top:2181px;width:283px}
.f-phone{left:459px;top:2181px;width:282px}
.f-email{left:752px;top:2181px;width:283px}
.f-msg{left:165px;top:2243px;width:870px;height:93px}
.send-btn{left:513px;top:2356px;width:174px;height:45px}
/* footer */
.footer{left:0;top:2472px;width:1200px;height:383px;background:var(--ink)}
.foot-brand{left:111px;top:2620px}
.foot-brand .brand-dot{width:72px;height:72px;border-width:6px}
.foot-brand .brand-name{font-size:20px}
.f-head{top:2532px;font-size:16px;font-weight:700;color:var(--white)}
.f-head::after{content:"";display:block;width:114px;height:3px;background:var(--green);margin-top:10px}
.f-links{top:2597px;list-style:none;font-size:14.5px;color:var(--white);line-height:37.7px}
.c-item{left:828px;display:flex;gap:16px;font-size:14.5px;color:var(--white);line-height:1.6}
.c-icon{width:38px;height:38px;border-radius:50%;background:var(--white);flex:none;display:flex;align-items:center;justify-content:center;margin-top:4px}
.c-item b{font-weight:700}
.f-divider{left:111px;top:2799px;width:978px;height:1px;background:#555}
.copy{left:0;top:2816px;width:1200px;text-align:center;font-size:13.5px;color:var(--white)}
.social{top:2808px;width:34px;height:34px;border-radius:50%;background:var(--white)}
.social.on{background:var(--green)}
</style>
</head>
<body>
<div class="page">
  <div class="abs topline"></div>

  <!-- header -->
  <div class="abs brand site-brand"><span class="brand-dot"></span><span class="brand-name">Dolores Quintana<br>Attorney at Law</span></div>
  <nav class="abs nav">
    <a class="active">HOME</a><a>ABOUT</a><a>SERVICES</a><a>LOCATION</a><a>FAQ</a><a>CONTACT</a>
  </nav>
  <div class="abs call-icon">
    <svg width="18" height="18" viewBox="0 0 24 24"><path fill="#46872f" d="M6.6 10.8a15.1 15.1 0 0 0 6.6 6.6l2.2-2.2c.3-.3.7-.4 1-.2 1.1.4 2.3.6 3.6.6.6 0 1 .4 1 1V20c0 .6-.4 1-1 1A17 17 0 0 1 3 4c0-.6.4-1 1-1h3.5c.6 0 1 .4 1 1 0 1.3.2 2.5.6 3.6.1.3 0 .7-.2 1z"/></svg>
  </div>
  <div class="abs call"><small>CALL ME:</small><strong>978-555-0142</strong></div>

  <!-- hero -->
  <svg class="abs hero-art" width="1200" height="600" viewBox="0 0 1200 600">
    <defs>
      <linearGradient id="heroTones" x1="0" y1="0" x2="0" y2="1">
        <stop offset="0" stop-color="#c9c6d2"/>
        <stop offset=".45" stop-color="#e3ddd6"/>
        <stop offset=".7" stop-color="#cfc2ad"/>
        <stop offset="1" stop-color="#b59f82"/>
      </linearGradient>
      <linearGradient id="heroFamily" x1="0" y1="0" x2="1" y2="0">
        <stop offset="0" stop-color="#e3ddd6" stop-opacity="0"/>
        <stop offset="1" stop-color="#6e5a4c" stop-opacity=".55"/>
      </linearGradient>
      <clipPath id="heroClip"><path d="M0 0H1200V398Q600 740 0 398Z"/></clipPath>
    </defs>
    <g role="img" aria-label="Photo of a smiling family with a child on the father's shoulders on a beach" clip-path="url(#heroClip)">
      <rect width="1200" height="600" fill="url(#heroTones)"/>
      <rect x="650" width="550" height="600" fill="url(#heroFamily)"/>
    </g>
    <path d="M0 398Q600 740 1200 398" fill="none" stroke="#46872f" stroke-width="5"/>
  </svg>
  <div class="abs dots"><i></i><i class="on"></i><i></i><i></i></div>
  <h1 class="abs hero-title">DOLORES QUINTANA<span>ATTORNEY AT LAW</span></h1>
  <div class="abs rule hero-rule"></div>
  <p class="abs hero-text">Dolores Quintana is a Solo Practitioner focusing her practice<br>on matters pertaining to family law and estate planning.</p>
  <div class="abs btn hero-btn">Request a free consultation</div>
  <div class="abs hero-badge">DQ</div>

  <!-- about -->
  <div class="abs portrait"><div role="img" aria-label="Black and white portrait photo of the attorney"></div></div>
  <h2 class="abs sec-title about-title">ABOUT <span>ME</span></h2>
  <div class="abs rule about-rule"></div>
  <div class="abs body-text about-text">
    <p>Dolores Quintana is a Solo Practitioner focusing her practice on matters pertaining to family law and estate planning.</p>
    <p>When I am retained, my clients are my priority. As a result, I work closely with each one to keep them informed through each step of the legal proceeding. Clients have always expressed to me how frustrating it is when attorneys don’t return phone calls. I understand this, as I am often met with the same challenges in the profession. I am proud of my practice and my reputation, and I return calls promptly.</p>
  </div>
  <div class="abs btn about-btn">Learn more</div>

  <!-- practice tabs -->
  <div class="abs tab tab-family">FAMILY LAW</div>
  <div class="abs tab tab-estate">ESTATE PLANNING</div>
  <div class="abs tab-pointer"></div>

  <h2 class="abs sec-title estate-title">ESTATE <span>PLANNING</span></h2>
  <div class="abs rule estate-rule"></div>
  <div class="abs body-text estate-text">
    <p>Whether you are creating an estate plan for the first time or updating your existing plan, I strive to make the estate planning process easy to understand, comfortable and comprehensive.</p>
    <p>Throughout the process of drafting an estate plan, additional professionals such as a financial planner, CPA and life insurance agent may become necessary resources in the handling of your assets. If this is necessary, I will advise you accordingly and provide you with a list of knowledgeable professionals to choose from.</p>
  </div>
  <div class="abs btn estate-btn">Learn more</div>
  <div class="abs estate-back"></div>
  <div class="abs estate-img" role="img" aria-label="Photo of a person in a yellow sweater working on a calculator over financial papers"></div>

  <!-- contact form -->
  <div class="abs contact"></div>
  <h2 class="abs sec-title contact-title">GET IN <span>TOUCH</span></h2>
  <div class="abs rule contact-rule"></div>
  <div class="abs field f-name">Full Name</div>
  <div class="abs field f-phone">Phone</div>
  <div class="abs field f-email">Email Address</div>
  <div class="abs field f-msg">Message</div>
  <div class="abs btn send-btn">Send message</div>

  <!-- footer -->
  <div class="abs footer"></div>
  <div class="abs brand foot-brand"><span class="brand-dot"></span><span class="brand-name">Dolores Quintana<br>Attorney at Law</span></div>

  <div class="abs f-head" style="left:439px">NAVIGATION</div>
  <ul class="abs f-links" style="left:440px"><li>HOME</li><li>About Me</li><li>Services</li><li>Location</li><li>Contact Me</li></ul>

  <div class="abs f-head" style="left:616px">QUICK LINKS</div>
  <ul class="abs f-links" style="left:617px"><li>FAQ</li><li>Privacy Policy</li><li>Terms &amp; Conditions</li><li>Disclaimer</li></ul>

  <div class="abs f-head" style="left:828px">CONTACT US</div>
  <div class="abs c-item" style="top:2597px">
    <span class="c-icon"><svg width="14" height="14" viewBox="0 0 24 24"><path fill="#46872f" d="M12 2a7 7 0 0 0-7 7c0 5.3 7 13 7 13s7-7.7 7-13a7 7 0 0 0-7-7zm0 9.5A2.5 2.5 0 1 1 12 6.5a2.5 2.5 0 0 1 0 5z"/></svg></span>
    <span>42 Harbor Lane Salem,<br>MA 01970</span>
  </div>
  <div class="abs c-item" style="top:2663px">
    <span class="c-icon"><svg width="14" height="14" viewBox="0 0 24 24"><path fill="#46872f" d="M6.6 10.8a15.1 15.1 0 0 0 6.6 6.6l2.2-2.2c.3-.3.7-.4 1-.2 1.1.4 2.3.6 3.6.6.6 0 1 .4 1 1V20c0 .6-.4 1-1 1A17 17 0 0 1 3 4c0-.6.4-1 1-1h3.5c.6 0 1 .4 1 1 0 1.3.2 2.5.6 3.6.1.3 0 .7-.2 1z"/></svg></span>
    <span><b>Call Me:</b><br>978-555-0142</span>
  </div>
  <div class="abs c-item" style="top:2729px">
    <span class="c-icon"><svg width="14" height="14" viewBox="0 0 24 24"><path fill="#46872f" d="M2 6l10 7 10-7v12H2zM2 4h20l-10 7z"/></svg></span>
    <span><b>Email Me:</b><br>doloresquintana@mail.com</span>
  </div>

  <div class="abs f-divider"></div>
  <div class="abs copy">© 2025 &nbsp;/ &nbsp;All Rights Reserved</div>
  <span class="abs social" style="left:974px"></span>
  <span class="abs social on" style="left:1013px"></span>
  <span class="abs social" style="left:1053px"></span>
</div>
</body>
</html>
```